Harborline Outpost Registry needs a web design

We are launching a new website and need a web design. The website is going to list every military base and installment around the world with information on each base such as a description of the base, the history of the base, contact information at the base, address, lat/long of the base, and any other relevant information including images of the base. We need a home page with navigation menu and the design of the military base page so that every military base page is formatted the same for the referenced information. We have included an example of the content that may be found on the base page(s). We are also going to have the information available in spanish.

We also wanted to mention we will be building this website in wordpress.

We also wanted to note that in the format of each base page, we will have a frequently asked questions section with answers.

```html
<!DOCTYPE html>
<html lang="en">
<head>
<meta charset="utf-8">
<title>Harborline Outpost Registry</title>
<link rel="stylesheet" href="https://fonts.googleapis.com/css2?family=Anton&family=Roboto:wght@400;500;700&display=swap">
<style>
:root{
  --yellow:#f5c853;
  --ink:#1c212b;
  --text:#6b6b6b;
  --dark:#222;
  --star:#f39a1e;
  --panel:#efefef;
  --white:#fff;
}
*{margin:0;padding:0;box-sizing:border-box}
html,body{width:1200px;height:3235px;overflow:hidden;background:var(--white);font-family:"Roboto",sans-serif;color:var(--dark)}
.page{position:relative;width:1200px;height:3235px}
.abs{position:absolute}
.display{font-family:"Anton",sans-serif;text-transform:uppercase;letter-spacing:-.5px;line-height:1}
.accent{color:var(--yellow)}
.topline{left:0;top:0;width:1200px;height:4px;background:var(--yellow)}
.hero{left:0;top:4px;width:1200px;height:648px;background:radial-gradient(ellipse at 30% 55%,#59613f 0%,#3e4230 45%,#25271f 100%)}
.hero-line{left:0;top:650px;width:1200px;height:4px;background:var(--yellow)}
.logo{left:110px;top:42px;font-family:"Anton",sans-serif;font-size:30px;color:var(--yellow);line-height:40px;white-space:nowrap}
.lang{left:932px;top:34px;display:flex;align-items:center;gap:10px;color:#fff;font-size:12px;font-weight:700}
.lang .dot{width:26px;height:26px;border-radius:50%;background:#e9e9e9}
.nav{top:80px;color:#fff;font-size:14px}
.nav a{position:absolute;color:#fff;text-decoration:none;white-space:nowrap;top:0}
.welcome{right:109px;top:200px;font-size:60px;color:var(--yellow);text-align:right}
.mbase{right:109px;top:288px;font-size:92px;color:#fff;text-align:right}
.btn{display:flex;align-items:center;justify-content:center;border-radius:22px;font-weight:700;font-size:15px}
.btn-yellow{left:962px;top:415px;width:128px;height:43px;background:var(--yellow);color:var(--ink)}
.search{left:111px;top:614px;width:977px;height:77px;background:var(--yellow);border-radius:38px}
.search-title{left:143px;top:631px;font-family:"Anton",sans-serif;font-size:29px;letter-spacing:-.3px;color:var(--ink);line-height:44px;white-space:nowrap}
.search-field{left:537px;top:628px;width:516px;height:48px;background:#fff;border-radius:8px}
.search-field .ph{position:absolute;left:46px;top:16px;font-size:13px;color:#777}
.search-field svg{position:absolute;left:20px;top:15px}
.search-btn{left:901px;top:632px;width:149px;height:41px;background:var(--ink);color:#fff;border-radius:6px;font-size:15px;display:flex;align-items:center;justify-content:center}
.h2{font-size:44px;color:var(--ink)}
.arrow{width:30px;height:30px;border-radius:50%;border:1.5px solid #555;display:flex;align-items:center;justify-content:center}
.lead{left:111px;top:828px;width:940px;font-size:14.5px;line-height:28px;color:var(--text)}
.card{width:233px;height:301px;background:#fff;box-shadow:0 2px 10px rgba(0,0,0,.08);border-radius:4px}
.card .ph-img{position:absolute;left:9px;top:13px;width:215px;height:168px;border-radius:6px}
.card .name{position:absolute;left:19px;top:204px;font-size:16px;font-weight:500;color:var(--ink);white-space:nowrap}
.rating{display:flex;align-items:center;gap:12px;font-size:11px;color:#666;white-space:nowrap}
.stars{color:var(--star);font-size:14px;letter-spacing:1px}
.card .rating{position:absolute;left:19px;top:234px}
.card .loc{position:absolute;left:19px;top:262px;font-size:12.5px;color:#666;white-space:nowrap}
.card .tel{position:absolute;left:19px;top:260px;font-family:"Anton",sans-serif;font-size:17px;color:var(--ink)}
.about-block{left:0;top:1390px;width:477px;height:508px;background:var(--yellow);border-radius:0 0 14px 0}
.about-photo{left:77px;top:1320px;width:477px;height:509px;border-radius:14px;background:linear-gradient(160deg,#6f7a5a,#3d4432 55%,#2a2e22)}
.about-title{left:636px;top:1395px;font-size:48px;color:var(--ink)}
.about-text{left:636px;width:455px;font-size:13.5px;line-height:28.3px;color:var(--text)}
.btn-dark{left:636px;top:1784px;width:129px;height:43px;background:var(--ink);color:#fff}
.pop{width:629px;height:222px;background:#fff;box-shadow:0 2px 10px rgba(0,0,0,.08);border-radius:4px}
.pop .ph-img{position:absolute;left:11px;top:12px;width:175px;height:197px;border-radius:4px}
.pop .ttl{position:absolute;left:214px;top:30px;font-size:22px;color:var(--ink);white-space:nowrap}
.pop .rating{position:absolute;left:214px;top:66px}
.pop .desc{position:absolute;left:214px;top:98px;width:225px;font-size:12.5px;line-height:21px;color:#666}
.pop .dsn{position:absolute;left:214px;top:170px;font-family:"Anton",sans-serif;font-size:15px;color:var(--ink);white-space:nowrap}
.pop .phone{position:absolute;right:30px;top:50px;font-family:"Anton",sans-serif;font-size:19px;color:var(--ink);white-space:nowrap}
.pop .coord{position:absolute;right:30px;top:98px;font-size:12px;line-height:24px;color:#555;text-align:right;white-space:nowrap}
.pop .dir{position:absolute;right:30px;top:148px;font-size:12px;color:var(--yellow);text-decoration:underline}
.reviews{left:771px;top:1992px;width:317px;height:541px;background:var(--panel);border-radius:4px}
.reviews .display{position:absolute;left:31px;top:28px;font-size:38px;color:var(--ink);white-space:nowrap}
.rev{position:absolute;left:32px;width:270px}
.avatar{position:absolute;left:0;top:0;width:54px;height:54px;border-radius:50%;background:linear-gradient(135deg,#7d8a66,#4c5640)}
.rev .who{position:absolute;left:77px;top:6px;font-size:15px;color:var(--ink)}
.rev .stars{position:absolute;left:77px;top:28px}
.rev .quote{position:absolute;left:0;top:68px;width:270px;font-size:11.5px;line-height:23.5px;color:#666}
.more{position:absolute;left:103px;top:502px;font-size:13px;font-weight:700;text-decoration:underline;color:var(--ink)}
.footer{left:0;top:2940px;width:1200px;height:295px;background:var(--ink);color:#fff}
.f-contact{position:absolute;top:86px;font-size:14.5px;display:flex;align-items:center;gap:12px;white-space:nowrap}
.f-sep{position:absolute;top:86px;font-size:14px}
.f-nav{position:absolute;top:150px;font-size:14px;white-space:nowrap}
.social{position:absolute;top:198px;width:30px;height:30px;border-radius:50%;background:var(--yellow)}
.copy{position:absolute;left:0;width:1200px;top:257px;text-align:center;font-size:11.5px}
</style>
</head>
<body>
<div class="page">

  <div class="abs hero" role="img" aria-label="Photo of a soldier with crossed arms in a dim concrete hangar"></div>
  <div class="abs topline"></div>
  <div class="abs hero-line"></div>

  <div class="abs logo">Harborline Outpost Registry</div>
  <div class="abs lang"><span class="dot"></span>Choose Language <span style="font-weight:400">&#8964;</span></div>
  <nav class="abs nav" style="left:0;width:1200px">
    <a style="left:526px">Home</a>
    <a style="left:623px">About Us</a>
    <a style="left:740px">Our Services</a>
    <a style="left:880px">Latest News</a>
    <a style="left:1018px">Contact Us</a>
  </nav>

  <div class="abs display welcome">Welcome to</div>
  <div class="abs display mbase">Military Base</div>
  <div class="abs btn btn-yellow">Get Started</div>

  <div class="abs search"></div>
  <div class="abs search-title">Search Our Military Base Here</div>
  <div class="abs search-field">
    <svg width="14" height="18" viewBox="0 0 14 18"><path d="M7 0C3.1 0 0 3.1 0 7c0 5 7 11 7 11s7-6 7-11c0-3.9-3.1-7-7-7zm0 9.5A2.5 2.5 0 1 1 7 4.5a2.5 2.5 0 0 1 0 5z" fill="#1c212b"/></svg>
    <span class="ph">Choose Location</span>
  </div>
  <div class="abs search-btn">Search Here</div>

  <div class="abs display h2" style="left:111px;top:766px">Featured <span class="accent">Listings</span></div>
  <div class="abs arrow" style="left:1020px;top:771px"><svg width="10" height="12" viewBox="0 0 10 12"><path d="M7 1 2 6l5 5" fill="none" stroke="#555" stroke-width="1.5"/></svg></div>
  <div class="abs arrow" style="left:1059px;top:771px;border-color:#111"><svg width="10" height="12" viewBox="0 0 10 12"><path d="M3 1l5 5-5 5" fill="none" stroke="#111" stroke-width="1.8"/></svg></div>
  <p class="abs lead">Sed ut perspiciatis unde omnis iste natus error sit voluptatem accusantium doloremque laudantium, totam rem aperiam, eaque ipsa quae ab illo inventore veritatis et quasi architecto beatae vitae dicta sunt explicabo. Nemo enim ipsam voluptatem quia voluptas sit aspernatur</p>

  <div class="abs card" style="left:111px;top:914px">
    <div class="ph-img" role="img" aria-label="Helicopters flying at sunset" style="background:linear-gradient(180deg,#6b8fb3,#e7a65a 70%,#3a3a38)"></div>
    <div class="name">Fort Calder Outpost</div>
    <div class="rating"><span class="stars">★★★★☆</span>19+ Reviews</div>
    <div class="loc">Calder Point, ME, United States</div>
  </div>
  <div class="abs card" style="left:359px;top:914px">
    <div class="ph-img" role="img" aria-label="Fighter jet on a runway at dusk" style="background:linear-gradient(180deg,#7c7468,#c98a4e 40%,#3b3e44)"></div>
    <div class="name">Lorem Lipsum Is Dummy</div>
    <div class="rating"><span class="stars">★★★★☆</span>19+ Reviews</div>
    <div class="loc">22Y, Lorem Lipsum, United States</div>
  </div>
  <div class="abs card" style="left:607px;top:914px">
    <div class="ph-img" role="img" aria-label="Soldier using a laptop in the field" style="background:linear-gradient(160deg,#3c5a2f,#1f3320 60%,#2f3a28)"></div>
    <div class="name">Lorem Lipsum Is Dummy</div>
    <div class="rating"><span class="stars">★★★★☆</span>19+ Reviews</div>
    <div class="loc">22Y, Lorem Lipsum, United States</div>
  </div>
  <div class="abs card" style="left:855px;top:914px">
    <div class="ph-img" role="img" aria-label="Aerial view of a large headquarters building" style="background:linear-gradient(160deg,#8a8f86,#a7a79b 50%,#6d7b5c)"></div>
    <div class="name">Lorem Lipsum Is Dummy</div>
    <div class="rating"><span class="stars">★★★★☆</span>19+ Reviews</div>
    <div class="loc">22Y, Lorem Lipsum, United States</div>
  </div>

  <div class="abs about-block"></div>
  <div class="abs about-photo" role="img" aria-label="Soldier in helmet and goggles holding a rifle among trees"></div>
  <div class="abs display about-title">About <span class="accent">Us</span></div>
  <p class="abs about-text" style="top:1465px">At vero eos et accusamus et iusto odio dignissimos ducimus qui blanditiis praesentium voluptatum deleniti atque corrupti quos dolores et quas molestias excepturi sint occaecati cupiditate non provident, similique sunt in culpa qui officia deserunt mollitia animi, id est laborum et dolorum fuga. Et harum quidem rerum facilis est et expedita distinctio.</p>
  <p class="abs about-text" style="top:1635px">Nam libero tempore, cum soluta nobis est eligendi optio cumque nihil impedit quo minus id quod maxime placeat facere possimus, omnis voluptas assumenda est, omnis dolor repellendus. Temporibus autem quibusdam et aut officiis debitis aut</p>
  <div class="abs btn btn-dark">Read More</div>

  <div class="abs display h2" style="left:111px;top:1988px;font-size:40px">Popular <span class="accent">This Week</span></div>

  <div class="abs pop" style="left:111px;top:2063px">
    <div class="ph-img" role="img" aria-label="Cargo aircraft on a tarmac under a cloudy sky" style="background:linear-gradient(180deg,#4f7fb4,#cfd9e3 55%,#6b6f72)"></div>
    <div class="display ttl">Fort Calder Outpost</div>
    <div class="rating"><span class="stars">★★★★☆</span>19+ Reviews</div>
    <div class="desc">Over the years, Fort Calder has become synonymous with its vital role as the Regional Reserve Supply Depot</div>
    <div class="dsn">DSN Number: (555) 018-7740</div>
    <div class="phone">(555) 014- 2290</div>
    <div class="coord">Latitude: 41.2210° N<br>Longitude: 70.1182°</div>
    <div class="dir">Directions</div>
  </div>
  <div class="abs pop" style="left:111px;top:2313px">
    <div class="ph-img" role="img" aria-label="Pilots seated in an attack helicopter" style="background:linear-gradient(160deg,#5d6d3a,#6c6a55 50%,#3d3b30)"></div>
    <div class="display ttl">Lorem Lipsum Is Dummy</div>
    <div class="rating"><span class="stars">★★★★☆</span>19+ Reviews</div>
    <div class="desc">Over the years, Fort Calder has become synonymous with its vital role as the Regional Reserve Supply Depot</div>
    <div class="dsn">DSN Number: (555) 018-7740</div>
    <div class="phone">(555) 014- 2290</div>
    <div class="coord">Latitude: 41.2210° N<br>Longitude: 70.1182°</div>
    <div class="dir">Directions</div>
  </div>

  <div class="abs reviews">
    <div class="display">Recent <span class="accent">Reviews</span></div>
    <div class="rev" style="top:98px">
      <div class="avatar" role="img" aria-label="Reviewer portrait"></div>
      <div class="who">Daniel Reyes</div>
      <div class="stars">★★★★☆</div>
      <p class="quote">“ I must explain to you how all this mistaken idea of denouncing pleasure and praising pain was born and I will give you a complete account of the system, and expound ”</p>
    </div>
    <div class="rev" style="top:274px">
      <div class="avatar" role="img" aria-label="Reviewer portrait"></div>
      <div class="who">Daniel Reyes</div>
      <div class="stars">★★★★☆</div>
      <p class="quote">“ I must explain to you how all this mistaken idea of denouncing pleasure ”</p>
    </div>
    <div class="rev" style="top:399px">
      <div class="avatar" role="img" aria-label="Reviewer portrait"></div>
      <div class="who">Daniel Reyes</div>
      <div class="stars">★★★★☆</div>
      <p class="quote">“ I must explain to you how ”</p>
    </div>
    <div class="more">View More Reviews</div>
  </div>

  <div class="abs card" style="left:111px;top:2563px">
    <div class="ph-img" role="img" aria-label="Soldier standing in a hangar doorway" style="background:linear-gradient(180deg,#2c3340,#55606e 55%,#23282f)"></div>
    <div class="name">Lorem Lipsum Dummy</div>
    <div class="rating"><span class="stars">★★★★☆</span>19+ Reviews</div>
    <div class="tel">+1 888 888 888</div>
  </div>
  <div class="abs card" style="left:359px;top:2563px">
    <div class="ph-img" role="img" aria-label="Fighter jet on a runway at sunset" style="background:linear-gradient(180deg,#4a5a6f,#d18e50 45%,#2e2f33)"></div>
    <div class="name">Lorem Lipsum Dummy</div>
    <div class="rating"><span class="stars">★★★★☆</span>19+ Reviews</div>
    <div class="tel">+1 888 888 888</div>
  </div>
  <div class="abs card" style="left:607px;top:2563px">
    <div class="ph-img" role="img" aria-label="Rows of parked aircraft seen from above" style="background:linear-gradient(160deg,#8c7a66,#6c7383 50%,#857462)"></div>
    <div class="name">Lorem Lipsum Dummy</div>
    <div class="rating"><span class="stars">★★★★☆</span>19+ Reviews</div>
    <div class="tel">+1 888 888 888</div>
  </div>
  <div class="abs card" style="left:855px;top:2563px">
    <div class="ph-img" role="img" aria-label="Military truck parked on a street" style="background:linear-gradient(160deg,#7a6a48,#5b5a38 50%,#8a7e66)"></div>
    <div class="name">Lorem Lipsum Dummy</div>
    <div class="rating"><span class="stars">★★★★☆</span>19+ Reviews</div>
    <div class="tel">+1 888 888 888</div>
  </div>

  <footer class="abs footer">
    <div class="f-contact" style="left:214px"><svg width="16" height="22" viewBox="0 0 14 18"><path d="M7 0C3.1 0 0 3.1 0 7c0 5 7 11 7 11s7-6 7-11c0-3.9-3.1-7-7-7zm0 9.5A2.5 2.5 0 1 1 7 4.5a2.5 2.5 0 0 1 0 5z" fill="#f5c853"/></svg>Calder Point, ME, United States</div>
    <div class="f-sep" style="left:478px">|</div>
    <div class="f-contact" style="left:540px"><svg width="16" height="16" viewBox="0 0 24 24"><path d="M6.6 10.8a15.1 15.1 0 0 0 6.6 6.6l2.2-2.2c.3-.3.7-.4 1-.2 1.1.4 2.3.6 3.6.6.6 0 1 .4 1 1V20c0 .6-.4 1-1 1A17 17 0 0 1 3 4c0-.6.4-1 1-1h3.5c.6 0 1 .4 1 1 0 1.3.2 2.5.6 3.6.1.3 0 .7-.2 1z" fill="#f5c853"/></svg>(555) 014- 2290</div>
    <div class="f-sep" style="left:729px">|</div>
    <div class="f-contact" style="left:792px"><svg width="16" height="12" viewBox="0 0 16 12"><rect width="16" height="12" rx="1" fill="#f5c853"/><path d="M0 1l8 6 8-6" fill="none" stroke="#1c212b" stroke-width="1.4"/></svg>info@harborlineregistry.com</div>
    <div class="f-nav" style="left:287px">Home</div>
    <div class="f-nav" style="left:361px">|</div>
    <div class="f-nav" style="left:402px">About Us</div>
    <div class="f-nav" style="left:496px">|</div>
    <div class="f-nav" style="left:536px">Our Services</div>
    <div class="f-nav" style="left:650px">|</div>
    <div class="f-nav" style="left:690px">Latest News</div>
    <div class="f-nav" style="left:803px">|</div>
    <div class="f-nav" style="left:844px">Contact Us</div>
    <div class="social" style="left:548px"></div>
    <div class="social" style="left:585px"></div>
    <div class="social" style="left:623px"></div>
    <div class="copy">© Copyright 2023 | All Rights Reserved.</div>
  </footer>

</div>
</body>
</html>
```